American cannabis tech company business card design

Pavrel.com is seeking a modern, professional, and brand-aligned business card that represents our company and its core values: Mission, Story, Values, and Impact. As an innovative cannabis company, we want a business card that is not only visually appealing but also serves as a representation of who we are and what we stand for.

Project Scope: Design a double-sided business card that integrates our brand identity and core values. Incorporate our key brand elements, ensuring a sleek and contemporary aesthetic. Visually reflect our core values (Mission, Story, Values, Impact) in a way that is engaging yet professional.

Target Market(s)

Vendors, third parties,

Contact Information for Business Card

Contact details (name, title, email, phone, website, etc.)

Font styles to use
Other font styles liked:
• Caslon, Centra

Colors

Designer to choose colors to be used in the design.

Requirements
Must have
• Pavrel.com logo and branding A creative yet clean way to integrate our core values (Mission, Story, Values, Impact) Modern typography and a well-structured layout
Nice to have
• forest green, grey, white, black
Should not have
• references to marijuana, leafs, plants, or related product

```html
<!DOCTYPE html>
<html lang="en">
<head>
<meta charset="utf-8">
<title>Pavrel.com Business Card</title>
<link href="https://fonts.googleapis.com/css2?family=Poppins:wght@400;600;700&display=swap" rel="stylesheet">
<style>
  :root {
    --forest: #17321a;
    --white: #ffffff;
    --ink: #1f1f1f;
    --divider: #b9b9b9;
    --backdrop: #9b9b9b;
  }
  html, body {
    margin: 0;
    padding: 0;
    width: 1093px;
    height: 1200px;
    overflow: hidden;
    background: var(--backdrop);
    font-family: "Poppins", sans-serif;
  }
  .stage {
    position: relative;
    width: 1093px;
    height: 1200px;
  }
  .card {
    position: absolute;
    left: 265px;
    width: 578px;
    height: 357px;
    border-radius: 24px;
    overflow: hidden;
  }
  .card--front {
    top: 226px;
    background: var(--white);
  }
  .card--back {
    top: 621px;
    background: var(--forest);
  }
  .front-band {
    position: absolute;
    left: 0;
    right: 0;
    bottom: 0;
    height: 13px;
    background: var(--forest);
  }
  .wordmark {
    position: absolute;
    font-weight: 700;
    letter-spacing: 0.5px;
    line-height: 1;
    margin: 0;
  }
  .card--front .wordmark {
    left: 40px;
    top: 150px;
    width: 222px;
    text-align: center;
    font-size: 50px;
    color: var(--forest);
  }
  .card--back .wordmark {
    left: 0;
    right: 0;
    top: 148px;
    text-align: center;
    font-size: 62px;
    color: var(--white);
  }
  .divider {
    position: absolute;
    left: 288px;
    top: 74px;
    width: 1px;
    height: 209px;
    background: var(--divider);
  }
  .identity {
    position: absolute;
    left: 313px;
    top: 98px;
  }
  .identity__name {
    margin: 0;
    font-size: 22px;
    font-weight: 600;
    line-height: 1.05;
    color: var(--forest);
  }
  .identity__title {
    margin: 0;
    font-size: 16.5px;
    font-weight: 400;
    line-height: 1.1;
    color: var(--ink);
  }
  .contacts {
    position: absolute;
    left: 312px;
    top: 175px;
    margin: 0;
    padding: 0;
    list-style: none;
  }
  .contacts__item {
    display: flex;
    align-items: center;
    height: 26.5px;
    font-size: 16px;
    color: var(--ink);
  }
  .contacts__icon {
    width: 24px;
    height: 24px;
    margin-right: 3px;
    flex: none;
  }
</style>
</head>
<body>
<main class="stage">
  <section class="card card--front" aria-label="Business card front">
    <p class="wordmark">PAVREL</p>
    <div class="divider"></div>
    <div class="identity">
      <h1 class="identity__name">DANIEL CARTER</h1>
      <p class="identity__title">Managing Director</p>
    </div>
    <ul class="contacts">
      <li class="contacts__item">
        <svg class="contacts__icon" viewBox="0 0 24 24" aria-hidden="true">
          <circle cx="12" cy="12" r="12" fill="var(--forest)"/>
          <path d="M8.2 6.5l1.8-.4 1.2 2.8-1.3 1c.6 1.4 1.7 2.5 3.1 3.1l1-1.3 2.8 1.2-.4 1.8c-.2.6-.8 1-1.4.9C10.9 15 8.5 12.6 7.4 8c-.1-.6.2-1.3.8-1.5z" fill="var(--white)"/>
          <path d="M13 7.2a4 4 0 0 1 3.8 3.8M13 5.4a5.8 5.8 0 0 1 5.6 5.6" stroke="var(--white)" stroke-width="1" fill="none"/>
        </svg>
        044-210 387 654
      </li>
      <li class="contacts__item">
        <svg class="contacts__icon" viewBox="0 0 24 24" aria-hidden="true">
          <circle cx="12" cy="12" r="12" fill="var(--forest)"/>
          <rect x="5.5" y="8" width="13" height="9" fill="var(--white)"/>
          <path d="M5.5 8l6.5 5 6.5-5M5.5 17l5-4.2M18.5 17l-5-4.2" stroke="var(--forest)" stroke-width="0.9" fill="none"/>
        </svg>
        hello@pavrel.com
      </li>
      <li class="contacts__item">
        <svg class="contacts__icon" viewBox="0 0 24 24" aria-hidden="true">
          <circle cx="12" cy="12" r="12" fill="var(--forest)"/>
          <g stroke="var(--white)" stroke-width="1" fill="none">
            <circle cx="12" cy="12" r="6"/>
            <ellipse cx="12" cy="12" rx="2.6" ry="6"/>
            <path d="M6 12h12M7 9h10M7 15h10"/>
          </g>
        </svg>
        www.pavrel.com
      </li>
    </ul>
    <div class="front-band"></div>
  </section>

  <section class="card card--back" aria-label="Business card back">
    <p class="wordmark">PAVREL</p>
  </section>
</main>
</body>
</html>
```